Business card for Luxury Portable Restroom Trailer company

We are a Luxury Portable Restroom Trailer Company Called FALCRIDGE HIRES. Based in Orange County California. We provide portable restroom trailers for events, such as, Weddings, Concerts, Charity events, Sporting events, Tournaments, Corporate events, ect. We rent and Sell the Luxury restrooms. Our colors are white, grey, and Orange. As you will see in the logo we uploaded.
There are 2 people in the company so the names and titles will change for the 3 people but card will remain the same. Here is the information for each Person: Dwight Penner CFO 555 318-0476
next Person: Leon Marchetti VP 555 318-0476
Next Person: Owen Marchetti CEO 555 318-0476
Information to include on the card: Luxury Restroom Trailers Rental and Sales. Weddings, Concerts, Charity, Sporting and Corp. Events.

```html
<!DOCTYPE html>
<html lang="en">
<head>
<meta charset="utf-8">
<title>FALCRIDGE HIRES – Business Card</title>
<link rel="stylesheet" href="https://fonts.googleapis.com/css2?family=Arimo:wght@400;700&display=swap">
<style>
  :root {
    --stage: #7b7b7b;
    --orange: #e06223;
    --grey: #4b4c4e;
    --white: #f5f5f6;
    --ink: #2f3033;
  }
  * { box-sizing: border-box; margin: 0; padding: 0; }
  html, body { width: 1200px; height: 900px; overflow: hidden; }
  body {
    background: var(--stage);
    font-family: "Arimo", Arial, sans-serif;
    position: relative;
  }
  .card {
    position: absolute;
    border-radius: 22px;
    box-shadow: 0 6px 18px rgba(0,0,0,0.25);
  }

  /* Back side */
  .card-back {
    left: 70px; top: 290px;
    width: 560px; height: 320px;
    background: var(--orange);
    display: flex; flex-direction: column;
    align-items: center; justify-content: center;
  }
  .brand-name {
    font-weight: 700;
    color: var(--grey);
    font-size: 46px;
    letter-spacing: 1px;
    line-height: 1;
  }
  .tagline {
    margin-top: 46px;
    color: var(--white);
    font-size: 15px;
    line-height: 1.35;
    text-align: center;
  }

  /* Front side */
  .card-front {
    left: 790px; top: 170px;
    width: 320px; height: 560px;
    background: var(--white);
    padding: 54px 40px;
    color: var(--ink);
  }
  .front-brand {
    font-weight: 700;
    color: var(--orange);
    font-size: 28px;
    letter-spacing: 0.5px;
    line-height: 1;
  }
  .person-name {
    margin-top: 44px;
    color: var(--orange);
    font-size: 26px;
    font-weight: 400;
    letter-spacing: 0.5px;
    text-transform: uppercase;
  }
  .person-title {
    margin-top: 6px;
    font-size: 15px;
    color: var(--grey);
  }
  .divider {
    width: 40px; height: 1px;
    background: var(--ink);
    margin: 34px 0 22px;
  }
  .info {
    font-size: 16px;
    line-height: 1.3;
    font-style: normal;
  }
</style>
</head>
<body>
  <section class="card card-back" aria-label="Card back">
    <div class="brand-name">FALCRIDGE HIRES</div>
    <p class="tagline">Luxury Restroom Trailers Rental and Sales<br>Weddings, Concerts, Charity, Sporting and Corp Events</p>
  </section>

  <section class="card card-front" aria-label="Card front">
    <div class="front-brand">FALCRIDGE HIRES</div>
    <h1 class="person-name">Dwight Penner</h1>
    <div class="person-title">CFO</div>
    <div class="divider"></div>
    <address class="info">2170 Harborview Lane<br>Tustin, CA 92780</address>
    <div class="divider"></div>
    <p class="info">555 318-0476<br>name@FALCRIDGE.com<br>www.FALCRIDGE.com</p>
  </section>
</body>
</html>
```